Customer Value Leaflet

We need a bi-fold brochure designing, based on the attached PDF wireframes. Our company name is brambleharvik.com (of which the logo is currently being designed). The corporate colour is orange (the exact shade of which we are happy to leave to the designers discretion).

The leaflet will distributed to customer experience experts and marketers so the design needs to be bright, engaging, clean and simple. Design is critical.

It Company

```html
<!DOCTYPE html>
<html lang="en">
<head>
<meta charset="utf-8">
<title>Customer Lifetime Value – brambleharvik.com</title>
<link href="https://fonts.googleapis.com/css2?family=Arimo:wght@400;700&display=swap" rel="stylesheet">
<style>
  :root {
    --peach: #fdeede;
    --cream: #fdf7ef;
    --orange: #f7941d;
    --ink: #1a1a1a;
    --label-black: #111111;
    --arrow-top: #9fcdea;
    --arrow-bottom: #8c8c8c;
    --figure-dark: #3a3a3a;
    --figure-mid: #6d6d6d;
    --basket-blue: #3b7fc4;
    --bird-blue: #45b4e6;
    --folder-gold: #e8b93a;
    --calendar-grey: #b9c3cf;
    --register-grey: #9a9a9a;
    --map-blue: #2f86c9;
    --board-grey: #e4e6e8;
  }
  * { box-sizing: border-box; margin: 0; padding: 0; }
  html, body { width: 1200px; height: 400px; overflow: hidden; }
  body { font-family: "Arimo", Arial, sans-serif; color: var(--ink); background: var(--cream); }

  .leaflet { position: relative; width: 1200px; height: 400px; background: var(--cream); }
  .story-panel { position: absolute; left: 0; top: 0; width: 805px; height: 364px; background: var(--peach); }
  .punchline-band { position: absolute; left: 0; top: 364px; width: 805px; height: 36px; background: var(--orange); }
  .punchline { position: absolute; top: 10px; font-size: 14px; color: var(--ink); }
  .punchline--setup { left: 14px; }
  .punchline--reveal { left: 540px; }

  .meet-label { position: absolute; top: 14px; height: 32px; background: var(--label-black); color: #fff;
    font-size: 13px; display: flex; align-items: center; justify-content: center; letter-spacing: .3px; }
  .meet-label--kim { left: 14px; width: 162px; }
  .meet-label--kevin { left: 183px; width: 163px; }

  .figure { position: absolute; border-radius: 40% 40% 12% 12%;
    background: linear-gradient(180deg, var(--figure-mid), var(--figure-dark)); }
  .figure--kim { left: 50px; top: 62px; width: 92px; height: 122px; }
  .figure--kevin { left: 222px; top: 62px; width: 92px; height: 122px; }

  .profile { position: absolute; top: 200px; width: 156px; text-align: center; font-size: 13px; line-height: 1.32; }
  .profile--kim { left: 18px; }
  .profile--kevin { left: 186px; }

  .event { position: absolute; font-size: 12px; line-height: 1.3; text-align: center; }
  .event--left { left: 436px; width: 134px; }
  .event--right { left: 626px; width: 150px; }
  .event--call { top: 12px; }
  .event--orders { top: 118px; }
  .event--lapse { top: 222px; }
  .event--purchase { top: 12px; }
  .event--tweets { top: 112px; }
  .event--regular { top: 222px; }

  .icon { position: absolute; border-radius: 6px; }
  .icon--kim { left: 485px; top: 56px; width: 34px; height: 40px; border-radius: 40% 40% 10% 10%;
    background: linear-gradient(180deg, var(--figure-mid), var(--figure-dark)); }
  .icon--basket { left: 474px; top: 160px; width: 58px; height: 44px; background: linear-gradient(180deg, #6aa8e0, var(--basket-blue)); }
  .icon--calendar { left: 479px; top: 280px; width: 48px; height: 50px; background: linear-gradient(180deg, #dfe5ec, var(--calendar-grey)); }
  .icon--register { left: 674px; top: 58px; width: 54px; height: 44px; background: linear-gradient(180deg, #c4c4c4, var(--register-grey)); }
  .icon--bird { left: 681px; top: 166px; width: 40px; height: 40px; background: var(--bird-blue); }
  .icon--folder { left: 674px; top: 278px; width: 54px; height: 48px; background: linear-gradient(180deg, #f4d170, var(--folder-gold)); }

  .timeline { position: absolute; left: 576px; top: 6px; }
  .timeline-label { font-family: "Arimo", Arial, sans-serif; font-size: 11px; fill: #ffffff; letter-spacing: .5px; }

  .pitch-title { position: absolute; left: 922px; top: 18px; font-size: 25px; font-weight: 700; }
  .pitch-board { position: absolute; left: 860px; top: 56px; width: 275px; height: 150px; border-radius: 4px;
    background: linear-gradient(180deg, var(--board-grey), #f6f7f8); border: 4px solid #cfd3d6; overflow: hidden; }
  .pitch-board__map { position: absolute; left: 24px; top: 14px; width: 220px; height: 90px; border-radius: 40px;
    background: var(--map-blue); opacity: .85; }
  .pitch-board__audience { position: absolute; left: 100px; top: 86px; width: 160px; height: 60px; border-radius: 30px 30px 4px 4px;
    background: linear-gradient(90deg, var(--orange), #5aa0d8); }
  .clv-term { position: absolute; left: 826px; top: 112px; width: 120px; font-size: 19px; font-weight: 700; line-height: 1.15;
    color: var(--orange); background: var(--cream); padding: 2px 4px; }
  .pitch-today { position: absolute; left: 935px; top: 212px; font-size: 15px; font-weight: 700; }
  .pitch-promise { position: absolute; left: 890px; top: 238px; width: 300px; text-align: center; font-size: 16px; font-weight: 700; line-height: 1.3; }
  .pitch-promise .accent { color: var(--orange); }
  .pitch-more { position: absolute; left: 890px; top: 292px; width: 300px; text-align: center; font-size: 14.5px; font-weight: 700; }
  .brand-name { position: absolute; left: 890px; top: 320px; width: 300px; text-align: center; font-size: 22px; font-weight: 700; color: var(--ink); }
  .brand-url { position: absolute; left: 890px; top: 364px; width: 300px; text-align: center; font-size: 16px; font-weight: 700; }
</style>
</head>
<body>
<main class="leaflet">
  <section class="story-panel">
    <div class="meet-label meet-label--kim">MEET KIM</div>
    <div class="meet-label meet-label--kevin">MEET KEVIN</div>
    <div class="figure figure--kim" role="img" aria-label="Illustration of Kim, a customer in dark glasses"></div>
    <div class="figure figure--kevin" role="img" aria-label="Illustration of Kevin, a customer in dark glasses"></div>
    <p class="profile profile--kim">Kim has purchased 3 items from you over the past 3 months @ £109 margin and you acquired her though a Searchly PPC campaign</p>
    <p class="profile profile--kevin">Kevin purchased an item last week @ £31 margin and you acquired him though a retargeting campaign</p>

    <p class="event event--left event--call">Kim calls you to return an item...</p>
    <div class="icon icon--kim" role="img" aria-label="Small illustration of Kim"></div>
    <p class="event event--left event--orders">places 4 more online orders...</p>
    <div class="icon icon--basket" role="img" aria-label="Illustration of a shopping basket"></div>
    <p class="event event--left event--lapse">then places another order but doesn't come back for a month</p>
    <div class="icon icon--calendar" role="img" aria-label="Illustration of a crossed-out calendar"></div>

    <p class="event event--right event--purchase">Kevin makes another purchase...</p>
    <div class="icon icon--register" role="img" aria-label="Illustration of a cash register"></div>
    <p class="event event--right event--tweets">then 2 more (and even tweets about how great your service is)...</p>
    <div class="icon icon--bird" role="img" aria-label="Social media post icon"></div>
    <p class="event event--right event--regular">and continues to make purchases on a bi-monthly basis</p>
    <div class="icon icon--folder" role="img" aria-label="Illustration of a folder with a pen"></div>

    <svg class="timeline" width="50" height="356" viewBox="0 0 50 356" aria-hidden="true">
      <defs>
        <linearGradient id="timeline-fill" x1="0" y1="0" x2="0" y2="1">
          <stop offset="0" stop-color="var(--arrow-top)"/>
          <stop offset="0.55" stop-color="#7fb6dc"/>
          <stop offset="1" stop-color="var(--arrow-bottom)"/>
        </linearGradient>
      </defs>
      <polygon points="9,0 41,0 41,300 50,300 25,356 0,300 9,300" fill="url(#timeline-fill)"/>
      <line x1="9" y1="112" x2="41" y2="112" stroke="#fff" stroke-width="1.5"/>
      <line x1="9" y1="238" x2="41" y2="238" stroke="#fff" stroke-width="1.5"/>
      <text class="timeline-label" transform="translate(29 84) rotate(-90)">+ 1 WEEK</text>
      <text class="timeline-label" transform="translate(29 205) rotate(-90)">+ 1 MONTH</text>
      <text class="timeline-label" transform="translate(29 318) rotate(-90)">+ 6 MONTHS</text>
    </svg>
  </section>

  <footer class="punchline-band">
    <p class="punchline punchline--setup">Right now you probably think Kim is your best customer…</p>
    <p class="punchline punchline--reveal">but really it is Kevin.</p>
  </footer>

  <aside class="pitch">
    <h2 class="pitch-title">By predicting</h2>
    <div class="pitch-board" role="img" aria-label="Illustration of a presentation board with a world map and an audience">
      <div class="pitch-board__map"></div>
      <div class="pitch-board__audience"></div>
    </div>
    <p class="clv-term">Customer Lifetime Value</p>
    <p class="pitch-today">today...</p>
    <p class="pitch-promise">...you can optimise<br>your business for <span class="accent">tomorrow</span></p>
    <p class="pitch-more">Find our more at</p>
    <p class="brand-name">brambleharvik</p>
    <p class="brand-url">www.brambleharvik.com</p>
  </aside>
</main>
</body>
</html>
```